Verdant Systems Business Card

want the back of card to be blue- with the logo in the center
front of card- info plus logo (info being mailing address, email address, and website address )
4 different names with titles to have on cards
1) Calvin Borsted - Owner
2) Naomi Trelvik- Customer Relationship Specialist
3) Felix Andrade- Vice President of Sales
4) Owen Markby- Chief Technology Officer

Target Market(s)

tech company in the government/probation office industry

Industry/Entity Type

Government Office

Contact Information for Business Card

1) Calvin Borsted - Owner

Colors
0355a3
ffffff

Requirements
Must have
• back side should be blue, with the logo placed in the center
• front side needs to include both the logo, as well as company info (info should include website address, email address, and mailing address)

```html
<!DOCTYPE html>
<html lang="en">
<head>
<meta charset="utf-8">
<title>Verdant Systems Business Card</title>
<link href="https://fonts.googleapis.com/css2?family=Crimson+Pro:wght@400;600&family=Roboto:wght@400&display=swap" rel="stylesheet">
<style>
  :root {
    --navy: #172a4f;
    --paper: #ffffff;
    --backdrop: #ececec;
    --text-grey: #4f4f4f;
    --title-grey: #8a8a8a;
    --rule: #c9c9c9;
  }
  html, body {
    margin: 0;
    padding: 0;
    overflow: hidden;
  }
  body {
    width: 1125px;
    height: 1200px;
    background: var(--backdrop);
    position: relative;
  }
  .card {
    position: absolute;
    left: 171px;
    width: 826px;
    height: 470px;
    box-sizing: border-box;
  }
  .card--front {
    top: 106px;
    background: var(--paper);
    border: 1px solid #dcdcdc;
  }
  .card--back {
    top: 639px;
    background: var(--navy);
  }
  .holder {
    position: absolute;
    right: calc(826px - 340px);
    top: 196px;
    text-align: right;
  }
  .holder__name {
    font-family: "Crimson Pro", serif;
    font-weight: 600;
    font-size: 35px;
    line-height: 1;
    color: var(--navy);
    margin: 0;
    white-space: nowrap;
  }
  .holder__title {
    font-family: "Roboto", sans-serif;
    font-size: 19px;
    color: var(--title-grey);
    margin-top: 6px;
  }
  .divider {
    position: absolute;
    left: 370px;
    top: 167px;
    width: 1px;
    height: 139px;
    background: linear-gradient(to bottom, rgba(0,0,0,0), var(--rule) 20%, var(--rule) 80%, rgba(0,0,0,0));
  }
  .contact {
    position: absolute;
    left: 404px;
    top: 181px;
    margin: 0;
    padding: 0;
    list-style: none;
  }
  .contact__item {
    display: flex;
    align-items: center;
    height: 26px;
    font-family: "Roboto", sans-serif;
    font-size: 19px;
    color: var(--text-grey);
  }
  .contact__icon {
    width: 16px;
    height: 16px;
    margin-right: 12px;
    fill: var(--navy);
    flex: none;
  }
  .brand {
    position: absolute;
    left: 0;
    right: 0;
    top: 180px;
    text-align: center;
    font-family: "Crimson Pro", serif;
    font-weight: 400;
    font-size: 62px;
    line-height: 1;
    color: var(--paper);
    letter-spacing: 1px;
  }
  .back-url {
    position: absolute;
    left: 0;
    right: 0;
    top: 404px;
    text-align: center;
    font-family: "Roboto", sans-serif;
    font-size: 19px;
    letter-spacing: 3px;
    color: var(--paper);
  }
</style>
</head>
<body>
  <section class="card card--front" aria-label="Card front">
    <div class="holder">
      <h1 class="holder__name">Calvin Borsted</h1>
      <div class="holder__title">Owner</div>
    </div>
    <div class="divider"></div>
    <ul class="contact">
      <li class="contact__item">
        <svg class="contact__icon" viewBox="0 0 16 16" aria-hidden="true"><path d="M3.6 1.2 5.8 3.8c.4.4.4 1-.1 1.4L4.6 6.1c.9 2 2.4 3.5 4.4 4.4l.9-1.1c.4-.5 1-.5 1.4-.1l2.6 2.2c.4.4.4 1 0 1.4l-1.3 1.3c-.6.6-1.6.8-2.4.4C6.3 13 3 9.7 1.4 5.8 1 5 1.2 4 1.8 3.4L3.1 2.1c.2-.5.3-.9.5-.9z"/></svg>
        <span>555-214-0736</span>
      </li>
      <li class="contact__item">
        <svg class="contact__icon" viewBox="0 0 16 16" aria-hidden="true"><path d="M4.5 0h7A1.5 1.5 0 0 1 13 1.5v13a1.5 1.5 0 0 1-1.5 1.5h-7A1.5 1.5 0 0 1 3 14.5v-13A1.5 1.5 0 0 1 4.5 0zm.3 2v10.5h6.4V2zM8 13.4a.9.9 0 1 0 0 1.8.9.9 0 0 0 0-1.8z"/></svg>
        <span>555-618-2049</span>
      </li>
      <li class="contact__item">
        <svg class="contact__icon" viewBox="0 0 16 16" aria-hidden="true"><path d="M1 3.5h14v9H1zm1.6 1.2L8 8.6l5.4-3.9v-.1H2.6zm0 1.5v5.1h10.8V6.2L8 10.1z"/></svg>
        <span>info@verdantsystems.com</span>
      </li>
      <li class="contact__item">
        <svg class="contact__icon" viewBox="0 0 16 16" aria-hidden="true"><path d="M8 .5a7.5 7.5 0 1 0 0 15A7.5 7.5 0 0 0 8 .5zM3.4 4.2c.9.3 1.6 1 1.5 2-.1.8.8 1.2 1.4 1.6.7.5.4 1.6-.3 2-.6.4-.6 1.4-.4 2.3A5.9 5.9 0 0 1 3.4 4.2zm6.3 9.6c.2-1 .9-1.5 1.6-2 .9-.6.4-1.9-.6-2-1-.1-1.9-.8-1.6-1.8.2-.8 1.2-.7 1.8-1.1.5-.4.2-1.3.8-1.6a5.9 5.9 0 0 1-2 8.5z"/></svg>
        <span>www.verdantsystems.com</span>
      </li>
    </ul>
  </section>

  <section class="card card--back" aria-label="Card back">
    <div class="brand">Verdant Systems</div>
    <div class="back-url">www.verdantsystems.com</div>
  </section>
</body>
</html>
```